banner ad

We're looking for a banner similar to the one shown on the attached file. The same 4 keywords, the same text up top, but with new formatting, design and perhaps color scheme. Looking for something to catch people's attention that will stand out on this particular page shown in the attached image. Our goal is to find a banner with a better click through rate than the current version.

```html
<!DOCTYPE html>
<html lang="en">
<head>
<meta charset="UTF-8">
<title>Blood Sugar Topics Banner</title>
<link href="https://fonts.googleapis.com/css2?family=Open+Sans:wght@700;800&display=swap" rel="stylesheet">
<style>
  :root {
    --page-bg: #ffffff;
    --tile-top: #e8313a;
    --tile-bottom: #b3111a;
    --tile-edge: #8e0c13;
    --label: #ffffff;
    --arrow-bg: #ffffff;
    --arrow-ink: #c1161e;
    --accent: #ffd23f;
    --band: #1f2a44;
    --band-stripe: #c1161e;
    --tile-shadow: rgba(31, 42, 68, 0.28);
  }
  * { margin: 0; padding: 0; box-sizing: border-box; }
  html, body {
    width: 1200px;
    height: 206px;
    overflow: hidden;
    background: var(--page-bg);
  }
  .banner {
    position: relative;
    width: 1200px;
    height: 206px;
    background: var(--page-bg);
    font-family: "Open Sans", Arial, sans-serif;
  }
  .topic-nav {
    position: absolute;
    left: 30px;
    top: 32px;
    width: 1140px;
    height: 104px;
    display: grid;
    grid-template-columns: repeat(4, 1fr);
    gap: 20px;
  }
  .topic-tile {
    position: relative;
    display: flex;
    align-items: center;
    justify-content: space-between;
    gap: 14px;
    height: 104px;
    padding: 0 20px 0 26px;
    border-radius: 14px;
    background: linear-gradient(160deg, var(--tile-top) 0%, var(--tile-bottom) 100%);
    border-bottom: 5px solid var(--tile-edge);
    box-shadow: 0 8px 16px var(--tile-shadow);
    color: var(--label);
    text-decoration: none;
    overflow: hidden;
  }
  .topic-tile::before {
    content: "";
    position: absolute;
    left: 0;
    top: 0;
    width: 6px;
    height: 100%;
    background: var(--accent);
  }
  .topic-label {
    font-weight: 800;
    font-size: 20px;
    line-height: 1.2;
    text-transform: uppercase;
    letter-spacing: 0.2px;
  }
  .topic-arrow {
    flex: 0 0 40px;
    width: 40px;
    height: 40px;
    border-radius: 50%;
    background: var(--arrow-bg);
    display: flex;
    align-items: center;
    justify-content: center;
  }
  .topic-arrow svg { width: 18px; height: 18px; }
  .footer-band {
    position: absolute;
    left: 0;
    top: 168px;
    width: 1200px;
    height: 38px;
    background: var(--band);
    border-top: 5px solid var(--band-stripe);
  }
</style>
</head>
<body>
  <div class="banner">
    <nav class="topic-nav">
      <a class="topic-tile" href="#">
        <span class="topic-label">Blood<br>Glucose</span>
        <span class="topic-arrow"><svg viewBox="0 0 18 18"><path d="M6 3l6 6-6 6" fill="none" stroke="#c1161e" stroke-width="3" stroke-linecap="round" stroke-linejoin="round"/></svg></span>
      </a>
      <a class="topic-tile" href="#">
        <span class="topic-label">Normal Blood<br>Sugar Range</span>
        <span class="topic-arrow"><svg viewBox="0 0 18 18"><path d="M6 3l6 6-6 6" fill="none" stroke="#c1161e" stroke-width="3" stroke-linecap="round" stroke-linejoin="round"/></svg></span>
      </a>
      <a class="topic-tile" href="#">
        <span class="topic-label">Blood Sugar<br>Levels Chart</span>
        <span class="topic-arrow"><svg viewBox="0 0 18 18"><path d="M6 3l6 6-6 6" fill="none" stroke="#c1161e" stroke-width="3" stroke-linecap="round" stroke-linejoin="round"/></svg></span>
      </a>
      <a class="topic-tile" href="#">
        <span class="topic-label">What Is Normal<br>Blood Sugar?</span>
        <span class="topic-arrow"><svg viewBox="0 0 18 18"><path d="M6 3l6 6-6 6" fill="none" stroke="#c1161e" stroke-width="3" stroke-linecap="round" stroke-linejoin="round"/></svg></span>
      </a>
    </nav>
    <div class="footer-band"></div>
  </div>
</body>
</html>
```